Home Remodeling company needs a business card design

we need a business card design for home remodeling company in hamilton county, indiana USA. we offers a wide range of construction services including whole house renovations, Design and Build Basements and Kitchen and Bathroom Remodeling . we would like to see designs for both site of business card that use the same color of the company logo and also including all information below :
1- Karim Feltous CEO / General Contractor
2- all company contacts Telephone numbers ( 1-888-DULOM-47 ) ( 317-555-0193) email address ( info@dulomhome.com) website ( www.dulomhome.com ) and social media logos (Facebook- twitter- google plus )
3- company logo
4- licensed . insured . bonded

```html
<!DOCTYPE html>
<html lang="en">
<head>
<meta charset="utf-8">
<title>Dulom Home Remodeling – Business Card</title>
<link href="https://fonts.googleapis.com/css2?family=Open+Sans:wght@400;600;700&display=swap" rel="stylesheet">
<style>
  :root {
    --page-bg: #e9e6e1;
    --card-white: #ffffff;
    --brand-red: #c8313c;
    --ink-dark: #3a3a3c;
    --ink-mid: #555558;
    --rule: #4a4a4c;
    --social-dark: #2f2f31;
    --on-red: #ffffff;
  }
  * { box-sizing: border-box; margin: 0; padding: 0; }
  html, body {
    width: 1200px; height: 950px; overflow: hidden;
    background: var(--page-bg);
    font-family: "Open Sans", Arial, sans-serif;
  }
  .sheet {
    width: 1200px; height: 950px;
    display: flex; flex-direction: column; align-items: center; justify-content: center;
    gap: 40px;
  }
  .card {
    width: 700px; height: 400px; position: relative;
    box-shadow: 0 6px 18px rgba(0,0,0,.18);
  }
  /* Front */
  .card-front { background: var(--card-white); }
  .brand {
    position: absolute; left: 56px; top: 52px;
    display: flex; align-items: center; gap: 12px;
  }
  .brand-square { width: 16px; height: 16px; background: var(--brand-red); }
  .brand-name {
    font-weight: 700; font-size: 58px; line-height: 1; letter-spacing: 2px;
    color: var(--ink-dark);
  }
  .header-rule {
    position: absolute; left: 56px; right: 56px; top: 150px;
    height: 1px; background: var(--rule);
  }
  .social {
    position: absolute; right: 56px; top: 106px;
    display: flex; gap: 6px;
  }
  .social-dot { width: 26px; height: 26px; border-radius: 50%; background: var(--social-dark); }
  .person { position: absolute; left: 56px; top: 196px; }
  .person-name { font-weight: 700; font-size: 28px; color: var(--ink-mid); }
  .person-title { font-weight: 400; font-size: 18px; color: var(--brand-red); margin-top: 2px; }
  .contacts {
    position: absolute; left: 56px; top: 272px;
    list-style: none;
  }
  .contacts li {
    display: flex; align-items: center; gap: 10px;
    font-size: 16px; color: var(--ink-mid); line-height: 26px;
  }
  .contacts svg { width: 14px; height: 14px; fill: var(--ink-dark); flex: none; }
  /* Back */
  .card-back {
    background: var(--brand-red);
    display: flex; align-items: center; justify-content: center;
  }
  .back-name {
    font-weight: 700; font-size: 64px; letter-spacing: 4px; color: var(--on-red);
  }
  .credentials {
    position: absolute; left: 40px; bottom: 30px;
    font-size: 15px; letter-spacing: 1.5px; color: var(--on-red);
  }
</style>
</head>
<body>
<main class="sheet">
  <section class="card card-front" aria-label="Business card front">
    <div class="brand">
      <span class="brand-square"></span>
      <span class="brand-name">DULOM</span>
    </div>
    <div class="social" aria-label="Social media links">
      <span class="social-dot"></span>
      <span class="social-dot"></span>
      <span class="social-dot"></span>
    </div>
    <div class="header-rule"></div>
    <div class="person">
      <p class="person-name">Karim Feltous</p>
      <p class="person-title">CEO / General Contractor</p>
    </div>
    <ul class="contacts">
      <li>
        <svg viewBox="0 0 16 16" aria-hidden="true"><path d="M3.5 1l2.5 3-1.5 2c1 2 3 4 5 5l2-1.5 3 2.5-1.5 2.5C7 15 1 9 1 2.5z"/></svg>
        1-888-DULOM-47
      </li>
      <li>
        <svg viewBox="0 0 16 16" aria-hidden="true"><path d="M4 1h8v14H4zM5.5 2.5v9h5v-9z"/></svg>
        317-555-0193
      </li>
      <li>
        <svg viewBox="0 0 16 16" aria-hidden="true"><path d="M1 3h14v10H1zM2.5 4.5v.6L8 9l5.5-3.9v-.6z"/></svg>
        info@dulomhome.com
      </li>
      <li>
        <svg viewBox="0 0 16 16" aria-hidden="true"><circle cx="8" cy="8" r="7"/><path d="M1 8h14M8 1c-3 3-3 11 0 14M8 1c3 3 3 11 0 14" stroke="#fff" stroke-width="1" fill="none"/></svg>
        www.dulomhome.com
      </li>
    </ul>
  </section>

  <section class="card card-back" aria-label="Business card back">
    <span class="back-name">DULOM</span>
    <p class="credentials">LICENSED | INSURED | BONDED</p>
  </section>
</main>
</body>
</html>
```